Business Card Design For A Cajun Seafood Restaurant

We are opening a cajun seafood restaurant in a week. We mainly serve cajun seafood which is orginally from Louisiana. We want design on both sides of a business card. I have menu on the website. You can go to www.reednkettle.example to check out our menu.

Restaurant name: Reed N' Kettle
Phone: +1 (555) 304-7712
Address: 48206 Ludlow Row, #7, Bexmoor Flats, Ca90000
Email: reednkettle@mailbox.example
Website: www.reednkettle.example

Maybe add social media icons (facebook, instagram) if looks nice on the business card.
facebook.com/reednkettle
instagram.com/reednkettle or @reednkettle

Attached is the logo and other business card samples that I like.

```html
<!DOCTYPE html>
<html lang="en">
<head>
<meta charset="utf-8">
<title>Reed N' Kettle – Business Card</title>
<link href="https://fonts.googleapis.com/css2?family=Open+Sans:wght@400;700&display=swap" rel="stylesheet">
<style>
  :root {
    --stage: #000000;
    --rust: #c0550a;
    --paper: #ffffff;
    --ink: #1a1a1a;
    --crab-light: #f7a23a;
    --crab-deep: #e8620f;
    --corn: #f3c93a;
  }
  * { margin: 0; padding: 0; box-sizing: border-box; }
  html, body { width: 1200px; height: 900px; overflow: hidden; background: var(--stage); }
  body { position: relative; font-family: "Open Sans", sans-serif; }

  .card { position: absolute; top: 200px; width: 310px; height: 502px; overflow: hidden; }

  .card-back {
    left: 265px;
    background: var(--rust);
    border-radius: 50px 0 50px 0;
    color: var(--paper);
  }
  .mascot-panel { position: absolute; left: 0; top: 0; }

  .contact-list { position: absolute; left: 24px; top: 276px; list-style: none; font-size: 13.5px; line-height: 19.5px; }
  .contact-list li { display: flex; align-items: center; gap: 7px; }
  .contact-list svg { width: 10px; height: 10px; flex: none; }

  .address { position: absolute; left: 23px; top: 357px; font-size: 13.5px; line-height: 20px; }

  .social-handle { position: absolute; left: 23px; top: 420px; font-size: 20px; font-weight: 700; }

  .card-front {
    left: 641px;
    background: var(--paper);
    border-radius: 50px 0 0 50px;
  }
  .front-mascot {
    position: absolute; left: 97px; top: 165px;
    width: 130px; height: 110px;
    border-radius: 50% 50% 40% 40%;
    background: radial-gradient(circle at 55% 30%, var(--corn) 0 22%, var(--crab-light) 40%, var(--crab-deep) 75%);
  }
  .wordmark {
    position: absolute; left: 0; width: 310px; top: 280px;
    text-align: center; color: var(--ink);
  }
  .wordmark-name { font-size: 24px; font-weight: 700; letter-spacing: 0.5px; }
  .wordmark-tagline { font-size: 12px; font-weight: 700; letter-spacing: 1px; margin-top: 2px; }
</style>
</head>
<body>

<section class="card card-back">
  <svg class="mascot-panel" width="310" height="245" viewBox="0 0 310 245">
    <path d="M55 0 H310 V195 C290 210 270 220 240 222 C200 228 180 240 160 235 C130 240 100 245 75 232 C55 222 50 190 58 160 C62 130 70 100 78 70 C82 40 70 20 55 0 Z" fill="var(--paper)"/>
    <g role="img" aria-label="Illustrated crab mascot holding an ear of corn above its head">
      <defs>
        <radialGradient id="mascotTone" cx="55%" cy="30%" r="70%">
          <stop offset="0" stop-color="var(--corn)"/>
          <stop offset="0.35" stop-color="var(--crab-light)"/>
          <stop offset="1" stop-color="var(--crab-deep)"/>
        </radialGradient>
      </defs>
      <ellipse cx="180" cy="110" rx="120" ry="100" fill="url(#mascotTone)"/>
    </g>
  </svg>

  <ul class="contact-list">
    <li>
      <svg viewBox="0 0 10 10"><path d="M2 0.5 L3.6 2.6 L2.8 3.6 C3.4 5 4.8 6.4 6.3 7.1 L7.3 6.3 L9.5 7.9 L8.6 9.5 C4.5 9.3 0.6 5.4 0.5 1.4 Z" fill="var(--paper)"/></svg>
      +1 (555) 304-7712
    </li>
    <li>
      <svg viewBox="0 0 10 10"><rect x="0.5" y="2" width="9" height="6.5" fill="var(--paper)"/><path d="M0.8 2.3 L5 5.6 L9.2 2.3" fill="none" stroke="var(--rust)" stroke-width="0.9"/></svg>
      reednkettle@mailbox.example
    </li>
    <li>
      <svg viewBox="0 0 10 10"><circle cx="5" cy="5" r="4.6" fill="var(--paper)"/><path d="M0.6 5 H9.4 M5 0.5 C2.8 3 2.8 7 5 9.5 M5 0.5 C7.2 3 7.2 7 5 9.5" fill="none" stroke="var(--rust)" stroke-width="0.8"/></svg>
      www.reednkettle.example
    </li>
  </ul>

  <p class="address">48206 Ludlow Row,<br>#7, Bexmoor Flats, Ca90000</p>

  <p class="social-handle">/reednkettle</p>
</section>

<section class="card card-front">
  <div class="front-mascot" role="img" aria-label="Crab mascot illustration holding corn"></div>
  <div class="wordmark">
    <p class="wordmark-name">REED N' KETTLE</p>
    <p class="wordmark-tagline">CAJUN SEAFOOD HOUSE</p>
  </div>
</section>

</body>
</html>
```